Business Card for brovaLINK

Create a Business Card with an existing logo for brovaLINK AG. We are a Information Technology company that does consulting and developing SW to automate business processes. The main colors are given from the logo.

Industry/Entity Type

Business

Requirements
Nice to have
• we use a a font style Century Gothic in our documents

```html
<!DOCTYPE html>
<html lang="en">
<head>
<meta charset="utf-8">
<title>brovaLINK Business Card</title>
<link href="https://fonts.googleapis.com/css2?family=Didact+Gothic&display=swap" rel="stylesheet">
<style>
  :root {
    --stage: #373737;
    --card: #ffffff;
    --field-tint: #f7f7f7;
    --ink-dark: #333333;
    --ink-mid: #666666;
    --band-green: #8dc63f;
    --band-green-soft: #b5d877;
    --band-blue: #2b7fc0;
    --band-blue-soft: #6fa8d8;
    --mark-circle: #2b7fc0;
  }
  html, body {
    margin: 0;
    padding: 0;
    width: 1200px;
    height: 1000px;
    overflow: hidden;
    background: var(--stage);
  }
  .stage {
    position: relative;
    width: 1200px;
    height: 1000px;
    font-family: "Didact Gothic", sans-serif;
  }
  .card {
    position: absolute;
    left: 98px;
    top: 175px;
    width: 1004px;
    height: 650px;
    background: var(--field-tint);
    overflow: hidden;
  }
  .band-top,
  .band-bottom {
    position: absolute;
    left: 0;
    width: 1004px;
  }
  .band-top {
    top: 0;
    height: 92px;
    background: linear-gradient(180deg, var(--band-green) 0%, var(--band-green-soft) 100%);
  }
  .band-bottom {
    bottom: 0;
    height: 84px;
    background: linear-gradient(0deg, var(--band-blue) 0%, var(--band-blue-soft) 100%);
  }
  .brand {
    position: absolute;
    left: 60px;
    top: 170px;
    width: 380px;
    text-align: center;
  }
  .brand-dot {
    display: block;
    width: 150px;
    height: 150px;
    margin: 0 auto 22px;
    border-radius: 50%;
    background: var(--mark-circle);
  }
  .brand-name {
    font-size: 58px;
    line-height: 1;
    color: var(--ink-dark);
    letter-spacing: 0.5px;
  }
  .contact {
    position: absolute;
    left: 468px;
    top: 240px;
    margin: 0;
  }
  .contact p {
    margin: 0;
    white-space: nowrap;
  }
  .contact-name,
  .contact-role {
    font-size: 36px;
    line-height: 42px;
    color: var(--ink-dark);
  }
  .contact-phone {
    font-size: 38px;
    line-height: 42px;
    color: var(--ink-mid);
    letter-spacing: 5px;
  }
  .contact-email {
    font-size: 36px;
    line-height: 44px;
    color: var(--ink-mid);
    letter-spacing: 0.5px;
  }
</style>
</head>
<body>
<div class="stage">
  <div class="card">
    <div class="band-top" role="img" aria-label="Green decorative wave band across the top edge"></div>
    <div class="band-bottom" role="img" aria-label="Blue decorative wave band across the bottom edge"></div>

    <div class="brand">
      <span class="brand-dot"></span>
      <div class="brand-name">brovaLINK</div>
    </div>

    <div class="contact">
      <p class="contact-name">Lena Varga</p>
      <p class="contact-role">Manager</p>
      <p class="contact-phone">07381 529 604</p>
      <p class="contact-email">lenavarga@brovalink.com</p>
    </div>
  </div>
</div>
</body>
</html>
```